I need a letterhead for a newsletter that will go out quarterly to the dentists of the 18th district. It is called "The Crestline Digest" We are in Amarillo TX and have this landmark in the photo as our most prominent feature. If it could be used, that would be cool.
This is a professional organization newsletter so the letterhead should be somewhat professional.

Target Market(s)

Dentists

Industry/Entity Type

Dental

Font styles to use
Serif

Colors

Designer to choose only greyscale colors for use in the design.

Requirements
Must have
• I want the title of "The Crestline Digest" to be the on top with the phrase "Cobalt Ridge Dental Society" written underneath.
Nice to have
• the photo incorporated could be incorporated in black and white or color along the bottom of the letterhead or with the title inside the photo.
Should not have
• I don't want it to be cartoony. I want it to be stylish and elegant and professional.

```html
<!DOCTYPE html>
<html lang="en">
<head>
<meta charset="utf-8">
<title>The Crestline Digest – Letterhead</title>
<link rel="stylesheet" href="https://fonts.googleapis.com/css2?family=EB+Garamond:wght@400;700&family=Open+Sans:wght@400;600;700&family=Great+Vibes&display=swap">
<style>
  :root {
    --backdrop: #e9e9e7;
    --paper: #ffffff;
    --ink: #151515;
    --ink-soft: #3a3a3a;
    --ink-muted: #7a7a7a;
    --rule: #444444;
    --swoosh-1: #d6d6d6;
    --swoosh-2: #b4b4b4;
    --swoosh-3: #8c8c8c;
    --swoosh-4: #5e5e5e;
  }
  * { box-sizing: border-box; margin: 0; padding: 0; }
  html, body {
    width: 1200px; height: 800px; overflow: hidden;
    background: var(--backdrop);
  }
  .canvas {
    position: relative; width: 1200px; height: 800px;
    display: flex; align-items: center; justify-content: center;
  }
  .letterhead {
    position: relative; width: 560px; height: 770px;
    background: var(--paper);
    box-shadow: 0 4px 18px rgba(0,0,0,0.12);
    overflow: hidden;
  }
  .corner-swoosh {
    position: absolute; top: 0; right: 0;
    width: 300px; height: 270px;
  }
  .masthead {
    position: absolute; left: 62px; top: 112px; width: 330px;
  }
  .masthead__title {
    font-family: "EB Garamond", serif; font-weight: 700;
    font-size: 27px; letter-spacing: 0.2px; line-height: 1;
    text-transform: uppercase; color: var(--ink);
  }
  .masthead__society {
    font-family: "EB Garamond", serif; font-weight: 400;
    font-size: 16px; color: var(--ink-muted);
    margin-top: 5px; letter-spacing: 0.2px;
  }
  .masthead__contact {
    font-family: "EB Garamond", serif; font-size: 7.5px;
    color: var(--ink-soft); margin-top: 8px;
    display: flex; gap: 9px; white-space: nowrap;
  }
  .masthead__rule {
    height: 1.5px; background: var(--rule);
    margin-top: 6px; width: 335px;
  }
  .letter {
    position: absolute; left: 72px; right: 72px; top: 300px;
    font-family: "Open Sans", sans-serif; font-size: 8.6px;
    line-height: 15.5px; color: var(--ink);
  }
  .letter__date { text-align: right; margin-bottom: 10px; }
  .letter__para { margin-bottom: 11px; text-indent: 16px; }
  .signature {
    position: absolute; right: 72px; top: 648px; text-align: left;
  }
  .signature__script {
    font-family: "Great Vibes", cursive; font-size: 24px;
    color: var(--ink); line-height: 1; margin-left: -30px;
  }
  .signature__name {
    font-family: "Open Sans", sans-serif; font-weight: 700;
    font-size: 8.5px; color: var(--ink); margin-top: 6px;
  }
  .signature__role {
    font-family: "Open Sans", sans-serif; font-size: 8.5px; color: var(--ink-soft);
  }
  .footer {
    position: absolute; left: 90px; right: 90px; top: 712px; text-align: center;
  }
  .footer__rule { height: 1.5px; background: var(--rule); }
  .footer__web {
    font-family: "EB Garamond", serif; font-size: 10px;
    letter-spacing: 2px; color: var(--ink-soft); margin-top: 9px;
  }
</style>
</head>
<body>
<main class="canvas">
  <article class="letterhead">
    <svg class="corner-swoosh" viewBox="0 0 300 270" aria-hidden="true">
      <path d="M20 0 C140 20 250 110 300 270 L300 0 Z" fill="var(--swoosh-1)"/>
      <path d="M60 0 C160 22 250 100 300 225 L300 0 Z" fill="var(--swoosh-2)"/>
      <path d="M100 0 C180 22 255 85 300 180 L300 0 Z" fill="var(--swoosh-3)"/>
      <path d="M140 0 C200 20 260 70 300 130 L300 0 Z" fill="var(--swoosh-4)"/>
    </svg>

    <header class="masthead">
      <h1 class="masthead__title">The Crestline Digest</h1>
      <p class="masthead__society">Cobalt Ridge Dental Society</p>
      <p class="masthead__contact">
        <span>A : 1480 W. Harlan Ave. Suite 210</span>
        <span>E: info@cobaltridgedental.org</span>
        <span>P: 806-555-0142</span>
      </p>
      <div class="masthead__rule"></div>
    </header>

    <section class="letter">
      <p class="letter__date">Date, 10 September, 2019</p>
      <p class="letter__para">This is a sample letter that has been placed to demonstrate typing remat (Your Company). letterhead design. When positioned properly, it will serve to work in harmony with all other elements letterhead. This letterhead design is meant to project an image</p>
      <p class="letter__para">This letterhead design is meant project an image of professionalism reliability. By using simple aligen we have created a very spacious feeling. The simplicity suggest rengththe spaciousnes contributes h aesthetics the layout. These basic qualities along with the (Your Company)</p>
      <p class="letter__para">look and helps reinforce the (Your Company) brand. letterhead design is meant to project an image p design. When positioned properly, it will serve to work in harmony all the other elements letterhead. sionalism and reliability.</p>
      <p class="letter__para">This letterhead design is based on the (Form of your logo) form (Your Company) logo. Each stationery we have created a very spacious feeling. The simplicity suggests strength the spaciousnes contribute part of the (Form of your logo).</p>
    </section>

    <div class="signature">
      <p class="signature__script">Daniel Marsh</p>
      <p class="signature__name">Daniel Marsh</p>
      <p class="signature__role">Manager</p>
    </div>

    <footer class="footer">
      <div class="footer__rule"></div>
      <p class="footer__web">www.cobaltridgedental.org</p>
    </footer>
  </article>
</main>
</body>
</html>
```